MRT Property - Business Cards

Looking for a business card & general letterhead, signage etc design for our new logo.

Colours:
000a20
0056a2
00b5ef
0088ce
68cef2

Fonts:
Poppins
Karla

Please keep look and feel of new brand - example in the zip package I sent.

```html
<!DOCTYPE html>
<html lang="en">
<head>
<meta charset="utf-8">
<title>MRT Property – Business Cards</title>
<link rel="stylesheet" href="https://fonts.googleapis.com/css2?family=Poppins:wght@400;500;700;800&display=swap">
<style>
  :root {
    --ink: #000a20;
    --navy: #0056a2;
    --sky: #00b5ef;
    --ocean: #0088ce;
    --ice: #68cef2;
    --card-blue: #1189cb;
    --card-blue-deep: #0a70b0;
    --paper: #ffffff;
    --backdrop: #c9c9c9;
  }
  * { box-sizing: border-box; margin: 0; padding: 0; }
  html, body {
    width: 1200px; height: 900px; overflow: hidden;
    background: var(--backdrop);
    font-family: "Poppins", sans-serif;
  }
  .canvas { position: relative; width: 1200px; height: 900px; }

  .card {
    position: absolute;
    width: 580px; height: 330px;
    border-radius: 30px;
    box-shadow: 0 6px 16px rgba(0,0,0,.25);
    overflow: hidden;
  }

  /* Front */
  .card--front {
    left: 110px; top: 110px;
    background: var(--card-blue);
    display: flex; align-items: center; justify-content: center; gap: 22px;
  }
  .front-mark {
    width: 64px; height: 64px; border-radius: 50%;
    background: var(--card-blue-deep);
  }
  .front-name {
    font-weight: 700; font-size: 60px; letter-spacing: 1px;
    color: var(--card-blue-deep);
  }

  /* Back */
  .card--back {
    left: 510px; top: 460px;
    background: var(--paper);
  }
  .brand {
    position: absolute; left: 42px; top: 112px;
    display: flex; align-items: center; gap: 12px;
  }
  .brand-dot { width: 30px; height: 30px; border-radius: 50%; background: var(--sky); }
  .brand-name { font-weight: 700; font-size: 30px; color: var(--navy); }

  .divider {
    position: absolute; left: 292px; top: 70px;
    width: 2px; height: 130px; background: var(--sky);
  }

  .contact { position: absolute; left: 318px; top: 70px; color: var(--ink); }
  .person-name {
    font-weight: 800; font-size: 22px; color: var(--navy);
    text-transform: uppercase; letter-spacing: .5px; line-height: 1.1;
  }
  .person-role { font-size: 13px; margin-bottom: 14px; }
  .contact-list { list-style: none; font-size: 13px; line-height: 1.55; }
  .contact-list li { display: flex; align-items: center; gap: 8px; }
  .contact-list svg { width: 13px; height: 13px; flex: none; }

  .address {
    position: absolute; left: 0; right: 0; bottom: 42px;
    text-align: center; font-size: 14px; color: var(--ink);
  }
</style>
</head>
<body>
<main class="canvas">

  <section class="card card--front" aria-label="Card front">
    <span class="front-mark"></span>
    <span class="front-name">MRT Property</span>
  </section>

  <section class="card card--back" aria-label="Card back">
    <div class="brand">
      <span class="brand-dot"></span>
      <span class="brand-name">MRT Property</span>
    </div>

    <span class="divider"></span>

    <div class="contact">
      <p class="person-name">Daniel Reyes</p>
      <p class="person-role">Managing Director</p>
      <ul class="contact-list">
        <li>
          <svg viewBox="0 0 24 24" aria-hidden="true"><path fill="var(--ocean)" d="M6.6 10.8a15 15 0 0 0 6.6 6.6l2.2-2.2c.3-.3.7-.4 1-.2 1.1.4 2.3.6 3.6.6.6 0 1 .4 1 1V20c0 .6-.4 1-1 1A17 17 0 0 1 3 4c0-.6.4-1 1-1h3.5c.6 0 1 .4 1 1 0 1.3.2 2.5.6 3.6.1.3 0 .7-.2 1z"/></svg>
          123 456 789
        </li>
        <li>
          <svg viewBox="0 0 24 24" aria-hidden="true"><rect x="2" y="5" width="20" height="14" rx="2" fill="var(--ocean)"/><path d="M3 6l9 7 9-7" fill="none" stroke="#fff" stroke-width="2"/></svg>
          info@mrtproperty.com
        </li>
        <li>
          <svg viewBox="0 0 24 24" aria-hidden="true"><circle cx="12" cy="12" r="10" fill="var(--ocean)"/><path d="M2 12h20M12 2c3 3 3 17 0 20M12 2c-3 3-3 17 0 20" fill="none" stroke="#fff" stroke-width="1.5"/></svg>
          www.mrtproperty.com
        </li>
      </ul>
    </div>

    <p class="address">Your address, City State, Zip 1234</p>
  </section>

</main>
</body>
</html>
```